Velmora Consulting Business

** Please add the content information from my old business card
1. I would like to see a two sided business card with both options with the 1st Option--Tallow Spire-new WHITE BACKGROUND LOGO
2 nd Option-Tallow Spire - new BLACK- Background Logo
3rd -Option a business card with my Photo on the card
Please add the new word to the card information:
EXECUTION
AS THE OWNER'S REP
WE AIM TO ACHIEVE YOUR
INFRASTRUCTURE VISION with
OUR SPECIALIZATION & EXECUTION in:

FUNDING Planning
BUSINESS Planning
INFRASTRUCTURE Planning
PROJECT Management
Since 2012
_____________________________________________________________________
I want to get spot uv raised printing. I was liking a a nice rich white linen paper stock with black writing & NOT A COLORED CARD other than a variety of white or black cards concept

```html
<!DOCTYPE html>
<html lang="en">
<head>
<meta charset="utf-8">
<title>Velmora Consulting – Business Card</title>
<link rel="stylesheet" href="https://fonts.googleapis.com/css2?family=Arimo:wght@400;700&display=swap">
<style>
  :root {
    --backdrop: #1b1b1c;
    --card-white: #f4f4f4;
    --card-dark: #242426;
    --ink: #1f1f1f;
    --red: #e02237;
    --white: #f2f2f2;
    --mark-grey: #4a4a4d;
  }
  * { box-sizing: border-box; margin: 0; padding: 0; }
  html, body {
    width: 1200px; height: 1059px; overflow: hidden;
    background: var(--backdrop);
    font-family: "Arimo", Arial, sans-serif;
  }
  .canvas { position: relative; width: 1200px; height: 1059px; }

  .card {
    position: absolute; width: 688px; height: 392px;
    border-radius: 24px; overflow: hidden;
  }
  .card--front { left: 256px; top: 89px; background: var(--card-white); color: var(--ink); }
  .card--back { left: 254px; top: 547px; background: var(--card-dark); color: var(--white); text-align: center; }

  /* front */
  .accent-bar { position: absolute; left: 0; top: 64px; width: 20px; height: 41px; background: var(--red); }
  .person { position: absolute; left: 39px; top: 60px; }
  .person__name { font-size: 24px; font-weight: 700; color: var(--red); line-height: 1.1; }
  .person__role { font-size: 16px; margin-top: 6px; letter-spacing: 0.2px; }

  .contact { position: absolute; left: 39px; top: 238px; list-style: none; }
  .contact__item { display: flex; align-items: center; height: 25.5px; font-size: 17px; }
  .contact__icon { width: 13px; height: 13px; margin-right: 7px; fill: var(--red); }

  .locations { position: absolute; left: 39px; top: 333px; font-size: 16.5px; }

  .brand-name {
    position: absolute; right: 38px; bottom: 40px;
    font-size: 30px; font-weight: 700; color: var(--ink); line-height: 1.1; text-align: right;
  }

  /* back */
  .brand-name--back {
    position: absolute; left: 0; right: 0; top: 60px;
    font-size: 34px; font-weight: 700; color: var(--mark-grey); text-align: center;
  }
  .pitch { position: absolute; left: 0; right: 0; top: 162px; }
  .pitch__lead { font-size: 19.4px; color: var(--red); line-height: 24px; }
  .pitch__line { font-size: 19.4px; line-height: 31px; }
  .rule { position: absolute; left: 0; right: 0; height: 1.5px; background: var(--red); }
  .rule--top { top: 258px; }
  .rule--bottom { top: 355px; }
  .services { position: absolute; left: 0; right: 0; top: 268px; font-size: 19.4px; line-height: 33px; }
  .services__sep { color: var(--red); margin: 0 6px; }
  .since {
    position: absolute; left: 50%; top: 343px; transform: translateX(-50%);
    padding: 0 9px; height: 25px; line-height: 23px;
    border: 1.5px solid var(--red); border-radius: 13px;
    background: var(--card-dark); font-size: 19px;
  }
</style>
</head>
<body>
<main class="canvas">

  <section class="card card--front" aria-label="Business card front">
    <div class="accent-bar"></div>
    <div class="person">
      <p class="person__name">Danielle Brookfield-Amari</p>
      <p class="person__role">CEO / LEAD PROJECT MANAGER</p>
    </div>
    <ul class="contact">
      <li class="contact__item">
        <svg class="contact__icon" viewBox="0 0 16 16" aria-hidden="true"><path d="M1 6c0-2 3-3 7-3s7 1 7 3v1h-4V5.5H5V7H1zM3 8h10l1.5 6h-13z"/></svg>
        555.010.0182
      </li>
      <li class="contact__item">
        <svg class="contact__icon" viewBox="0 0 16 16" aria-hidden="true"><path d="M1 6l7-5 7 5v9H1zM2.5 7v6.5h11V7L8 11z"/></svg>
        dani@velmora.ca
      </li>
      <li class="contact__item">
        <svg class="contact__icon" viewBox="0 0 16 16" aria-hidden="true"><circle cx="8" cy="8" r="7"/></svg>
        www.velmora.ca
      </li>
    </ul>
    <p class="locations">Wrenfield Office • Calderton Office</p>
    <p class="brand-name">Velmora<br>Consulting</p>
  </section>

  <section class="card card--back" aria-label="Business card back">
    <p class="brand-name--back">Velmora Consulting</p>
    <div class="pitch">
      <p class="pitch__lead">AS THE OWNER'S REP</p>
      <p class="pitch__line">WE AIM TO ACHIEVE YOUR INFRASTRUCTURE VISION</p>
      <p class="pitch__line">with OUR SPECIALIZATION &amp; EXECUTION in:</p>
    </div>
    <div class="rule rule--top"></div>
    <div class="services">
      <p>FUNDING Planning<span class="services__sep">|</span>BUSINESS Planning</p>
      <p>INFRASTRUCTURE Planning<span class="services__sep">|</span>PROJECT Management</p>
    </div>
    <div class="rule rule--bottom"></div>
    <p class="since">Since 2012</p>
  </section>

</main>
</body>
</html>
```